QP Fiduciary Website Redesign Contest

We want to refresh our website to be more insitutional, professional for an international audience. We have designed a new logo for this purpose and that has been attached. A full brand brief and positioning statement has also been attached. Please read through all the documents carefully before designing. The old website is found here: https://qp-fiduciary.example/

Target Market(s)

Actuaries and associated businesses internationally

Industry/Entity Type

professional services - actuaries

Number of Pages Required

3 page

Font styles to use
Sans Serif

Colors
0054AA
0677BA
7BADD7
CADEEF
E8F1F8
0094D4
00A9DD
6FCCEA
C7EBF8
E9F6FB
F0912C
F2A743
F7CA91
FBE8D2
FDF5EE
EE7325
F08F49
F5BC92
FAE3D3
FDF4ED
EB3D1F
EC4F4E
F09395
F8D3D4
FCEDEE

Requirements
Must have
• blues and greens to match the logo color, complimentary colors, navigation
Nice to have
• old site: https://qp-fiduciary.example/

```html
<!DOCTYPE html>
<html lang="en">
<head>
<meta charset="utf-8">
<title>QP Fiduciary — Actuarial Software</title>
<link rel="stylesheet" href="https://fonts.googleapis.com/css2?family=Poppins:wght@300;400;500;600;700&display=swap">
<style>
:root{
  --navy:#0b1a38;
  --ink:#111827;
  --body:#3b4252;
  --blue:#0054AA;
  --blue-mid:#0677BA;
  --sky:#CADEEF;
  --sky-soft:#E8F1F8;
  --teal:#0a9e86;
  --teal-soft:#dff3ef;
  --orange:#F07A1E;
  --orange-soft:#FBE8D2;
  --white:#ffffff;
  --grad:linear-gradient(90deg,#0a9e86 0%,#0677BA 55%,#0054AA 100%);
}
*{box-sizing:border-box;margin:0;padding:0}
html,body{width:1200px;height:4196px;overflow:hidden}
body{font-family:"Poppins",sans-serif;color:var(--ink);background:var(--white);position:relative}
.abs{position:absolute}
.logo{font-weight:500;font-size:26px;letter-spacing:1px;color:var(--navy);display:flex;align-items:center;gap:10px}
.logo .dot{width:14px;height:14px;border-radius:50%;background:var(--orange)}
.nav{left:352px;top:33px;display:flex;gap:24px;font-size:13px;font-weight:500;color:var(--ink)}
.btn{display:flex;align-items:center;justify-content:space-between;border-radius:40px;color:#fff;font-size:12.5px;font-weight:500;text-transform:uppercase;background:var(--grad);padding:0 5px 0 16px}
.btn .arr{width:34px;height:34px;border-radius:50%;background:#fff;display:flex;align-items:center;justify-content:center}
.btn-orange{background:var(--orange);justify-content:center;padding:0 14px;font-size:12.5px}
.pill{border:1px solid #7fd0c0;background:var(--teal-soft);color:var(--teal);font-size:12px;font-weight:500;border-radius:20px;display:flex;align-items:center;justify-content:center;text-transform:uppercase}
.h2{font-size:38px;font-weight:400;color:var(--ink);line-height:1.15}
.h2 b{font-weight:700}
.center{text-align:center;left:0;width:1200px}
.lead{font-size:13px;color:var(--ink);line-height:1.65}
.hero-img{left:0;top:82px;width:1200px;height:566px;background:linear-gradient(120deg,#2b3340 0%,#5b6778 40%,#9aa7b6 62%,#3c4656 100%)}
.hero-shade{left:0;top:82px;width:1200px;height:566px;background:linear-gradient(180deg,rgba(0,0,0,.05) 30%,rgba(0,0,0,.55) 100%)}
.hero h1{font-size:41px;font-weight:300;color:#fff;line-height:1.2}
.hero h1 b{font-weight:700}
.feature{width:210px;height:166px;background:#fff;border-radius:14px;box-shadow:0 6px 18px rgba(20,40,80,.12);padding:58px 16px 0}
.feature h3{font-size:15px;font-weight:500;line-height:1.4;margin-bottom:6px}
.feature p{font-size:11.5px;line-height:1.6;color:var(--body)}
.icon{width:62px;height:62px;border-radius:12px;display:flex;align-items:center;justify-content:center;box-shadow:0 4px 10px rgba(0,0,0,.15)}
.i-blue{background:linear-gradient(160deg,#1f7fe0,#0054AA)}
.i-orange{background:linear-gradient(160deg,#f7a14a,#EE7325)}
.i-navy{background:linear-gradient(160deg,#1f5fb8,#0b3d8a)}
.i-teal{background:linear-gradient(160deg,#1bbf9a,#0a8d73)}
.sol-bg{left:0;top:1157px;width:1200px;height:611px;background:linear-gradient(100deg,#e3f3f0 0%,#e6eff8 100%)}
.sol-card{background:#fff;border-radius:10px;box-shadow:0 6px 18px rgba(20,40,80,.1);padding:16px}
.sol-card h3{font-size:15px;font-weight:500;margin:10px 0 6px}
.sol-card p{font-size:11.5px;line-height:1.6;color:var(--body)}
.sol-card .go{position:absolute;right:12px;bottom:12px;width:22px;height:22px;border-radius:4px;background:var(--teal);display:flex;align-items:center;justify-content:center}
.ch-label{font-size:14px;font-weight:500;line-height:1.5}
.ch-icon{width:70px;height:70px;border-radius:50%;display:flex;align-items:center;justify-content:center}
.c-blue{background:var(--blue)}
.c-teal{background:#13a883}
.hub{left:454px;top:2079px;width:293px;height:138px;border-radius:69px;background:#fff;box-shadow:0 8px 24px rgba(20,40,80,.12);display:flex;align-items:center;justify-content:center}
.node{width:11px;height:11px;border-radius:50%;border:2px solid var(--blue);background:#fff}
.node.t{border-color:var(--teal)}
.ins-bg{left:0;top:2458px;width:1200px;height:826px;background:linear-gradient(120deg,#e6effa 0%,#e9f4f3 100%)}
.post{width:281px;height:422px;background:#fff;border-radius:10px;box-shadow:0 6px 18px rgba(20,40,80,.08)}
.post .ph{position:absolute;left:10px;top:10px;width:261px;height:205px;border-radius:8px}
.post .date{position:absolute;left:15px;top:228px;font-size:11.5px;font-weight:500;display:flex;gap:7px;align-items:center}
.post .date i{width:13px;height:13px;border-radius:2px;background:var(--blue);display:block}
.post h3{position:absolute;left:15px;top:253px;width:250px;font-size:13.5px;font-weight:600;line-height:1.55}
.post p{position:absolute;left:15px;width:250px;font-size:12px;line-height:1.75;color:var(--body)}
.post p u{text-decoration:underline}
.post .more{position:absolute;left:15px;top:360px;width:111px;height:38px;border:1.5px solid #f5b98a;border-radius:6px;color:var(--orange);font-size:12px;font-weight:500;display:flex;align-items:center;justify-content:center}
.slide{width:36px;height:36px;border-radius:50%;display:flex;align-items:center;justify-content:center}
.cta{left:142px;top:3375px;width:916px;height:373px;border-radius:30px;overflow:hidden;background:linear-gradient(100deg,#0aa489 0%,#0a8f96 45%,#0677BA 100%)}
.cta-img{position:absolute;left:509px;top:0;width:407px;height:373px;background:linear-gradient(135deg,#f1f3f5 0%,#c7cfd8 45%,#8f9aa7 100%)}
.cta-fade{position:absolute;left:449px;top:0;width:140px;height:373px;background:linear-gradient(90deg,#0a8aa0 0%,rgba(10,138,160,0) 100%)}
.cta .pill-w{position:absolute;left:45px;top:71px;width:163px;height:30px;border:1px solid rgba(255,255,255,.7);border-radius:20px;color:#fff;font-size:12px;display:flex;align-items:center;justify-content:center}
.cta h2{position:absolute;left:45px;top:118px;font-size:38px;font-weight:300;color:#fff;line-height:1.15}
.cta h2 b{font-weight:700}
.cta p{position:absolute;left:45px;top:212px;font-size:12.5px;color:#fff;line-height:1.7;width:440px}
.cta .btn-w{position:absolute;left:45px;top:265px;width:305px;height:44px;border-radius:40px;background:#fff;color:var(--ink);font-size:12.5px;font-weight:500;display:flex;align-items:center;justify-content:space-between;padding:0 5px 0 16px}
.cta .btn-w .arr{width:34px;height:34px;border-radius:50%;background:var(--grad);display:flex;align-items:center;justify-content:center}
.footer{left:0;top:3834px;width:1200px;height:362px;background:var(--navy);color:#fff}
.footer h4{font-size:17px;font-weight:500}
.footer .links{font-size:13px;line-height:2.15;color:#d9e0ec}
.footer .txt{font-size:12px;line-height:1.65;color:#d9e0ec}
.soc{display:flex;align-items:center;gap:10px;font-size:13px;color:#d9e0ec;height:41px}
.soc span{width:28px;height:28px;border-radius:50%;border:1.5px solid #fff;display:block}
.soc span.on{background:#13a883;border-color:#13a883}
</style>
</head>
<body>

<!-- Header -->
<header>
  <div class="abs logo" style="left:93px;top:26px"><span class="dot"></span>QP FIDUCIARY</div>
  <nav class="abs nav"><span>PLATFORM</span><span>SOLUTIONS</span><span>INSIGHTS</span><span>COMPANY</span><span>CONTACT</span></nav>
  <div class="abs btn btn-orange" style="left:788px;top:20px;width:270px;height:42px">REQUEST A TECHNICAL WALKTHROUGH</div>
</header>

<!-- Hero -->
<section class="hero">
  <div class="abs hero-img" role="img" aria-label="Professionals reviewing printed financial charts with a pen and tablet"></div>
  <div class="abs hero-shade"></div>
  <h1 class="abs center" style="top:398px">Actuarial <b>Software</b> For Structured,<br>Auditable <b>Financial Analysis.</b></h1>
  <p class="abs center" style="top:502px;font-size:12.5px;color:#fff;line-height:1.65">QP Fiduciary Develops Software That Translates Established Actuarial<br>Methodologies Into Disciplined, Decision-Ready Tools.</p>
  <div class="abs btn" style="left:448px;top:557px;width:301px;height:42px">REQUEST A TECHNICAL WALKTHROUGH
    <span class="arr"><svg width="18" height="18" viewBox="0 0 24 24"><path d="M4 12h15M13 6l6 6-6 6" stroke="#0054AA" stroke-width="2.4" fill="none" stroke-linecap="round"/></svg></span></div>
</section>

<!-- Platform overview -->
<section>
  <div class="abs pill" style="left:510px;top:711px;width:180px;height:31px">PLATFORM OVERVIEW</div>
  <h2 class="abs h2 center" style="top:750px">Built For Actuarial <b>Excellence</b></h2>
  <p class="abs lead center" style="top:805px">Our Platform Delivers Structured Workflows, Transparent Assumptions, And Complete Auditability<br>—Enabling Confident, Governance-Ready Financial Analysis.</p>

  <div class="abs feature" style="left:142px;top:900px"><h3>Structured Workflows</h3><p>Disciplined Processes That Guide Analysis From Input To Output With Clear, Repeatable Steps.</p></div>
  <div class="abs feature" style="left:377px;top:900px"><h3>Transparency<br>of Assumptions</h3><p>Every Assumption Is Documented, Visible, And Traceable Throughout.</p></div>
  <div class="abs feature" style="left:613px;top:900px"><h3>Auditability</h3><p>Complete Audit Trails With Version Control And Comprehensive Documentation At Every Step.</p></div>
  <div class="abs feature" style="left:849px;top:900px"><h3>Governance</h3><p>Built-In Controls And Approval Workflows That Ensure Regulatory Compliance.</p></div>

  <div class="abs icon i-blue" style="left:160px;top:870px"><svg width="34" height="34" viewBox="0 0 24 24" fill="none" stroke="#fff" stroke-width="1.6"><rect x="3" y="3" width="18" height="8" rx="1"/><path d="M12 11v4M6 15h12M6 15v3M12 15v3M18 15v3"/><rect x="4" y="18" width="4" height="3"/><rect x="10" y="18" width="4" height="3"/><rect x="16" y="18" width="4" height="3"/></svg></div>
  <div class="abs icon i-orange" style="left:396px;top:870px"><svg width="34" height="34" viewBox="0 0 24 24" fill="none" stroke="#fff" stroke-width="1.6"><circle cx="12" cy="12" r="8"/><path d="M12 4v8l6 4"/></svg></div>
  <div class="abs icon i-navy" style="left:631px;top:870px"><svg width="34" height="34" viewBox="0 0 24 24" fill="none" stroke="#fff" stroke-width="1.6"><rect x="5" y="3" width="12" height="16" rx="1"/><path d="M8 7h6M8 10h6"/><circle cx="15" cy="16" r="4"/><path d="M13.3 16l1.2 1.2 2.2-2.2"/></svg></div>
  <div class="abs icon i-teal" style="left:867px;top:870px"><svg width="34" height="34" viewBox="0 0 24 24" fill="none" stroke="#fff" stroke-width="1.6"><path d="M3 10l9-6 9 6M5 10v8M9 10v8M15 10v8M19 10v8M3 20h18"/></svg></div>
</section>

<!-- Solutions -->
<section>
  <div class="abs sol-bg"></div>
  <div class="abs pill" style="left:142px;top:1322px;width:148px;height:31px">OUR SOLUTIONS</div>
  <h2 class="abs h2" style="left:142px;top:1363px">Comprehensive<br><b>Actuarial Suite</b></h2>
  <p class="abs lead" style="left:142px;top:1456px">Three Integrated Solution Areas Designed To Address The<br>Full Spectrum Of Actuarial Analysis Needs.</p>
  <div class="abs btn" style="left:142px;top:1522px;width:306px;height:43px">REQUEST A TECHNICAL WALKTHROUGH
    <span class="arr"><svg width="18" height="18" viewBox="0 0 24 24"><path d="M4 12h15M13 6l6 6-6 6" stroke="#0054AA" stroke-width="2.4" fill="none" stroke-linecap="round"/></svg></span></div>

  <svg class="abs" style="left:600px;top:1270px" width="420" height="240" viewBox="0 0 420 240" fill="none">
    <path d="M200 10 L200 40" stroke="#0a9e86" stroke-width="14"/>
    <path d="M70 200 Q110 240 130 220" stroke="#0a9e86" stroke-width="10"/>
    <path d="M340 200 Q310 240 290 220" stroke="#0054AA" stroke-width="10"/>
  </svg>

  <div class="abs sol-card" style="left:547px;top:1242px;width:246px;height:223px">
    <svg width="62" height="56" viewBox="0 0 62 56" fill="none" stroke="#0054AA" stroke-width="3"><rect x="14" y="4" width="30" height="40" rx="3"/><path d="M20 14h18M20 22h18M20 30h10"/><circle cx="46" cy="42" r="10"/><path d="M2 52h22"/></svg>
    <h3>Reserving &amp; Valuation</h3>
    <p>Comprehensive Reserve Calculations And Liability Valuations With Transparent Methodology Documentation And Multi-Standard Support.</p>
    <span class="go"><svg width="12" height="12" viewBox="0 0 24 24"><path d="M6 18L18 6M9 6h9v9" stroke="#fff" stroke-width="2.6" fill="none"/></svg></span>
  </div>
  <div class="abs sol-card" style="left:811px;top:1242px;width:247px;height:223px">
    <svg width="62" height="56" viewBox="0 0 62 56" fill="none" stroke="#0054AA" stroke-width="3"><rect x="8" y="18" width="44" height="30" rx="6"/><circle cx="22" cy="33" r="5"/><circle cx="40" cy="33" r="5"/><path d="M24 6l10 10"/></svg>
    <h3>Pricing</h3>
    <p>Sophisticated Pricing Models That Balance Profitability Targets With Competitive Positioning And Regulatory Requirements.</p>
    <span class="go"><svg width="12" height="12" viewBox="0 0 24 24"><path d="M6 18L18 6M9 6h9v9" stroke="#fff" stroke-width="2.6" fill="none"/></svg></span>
  </div>
  <div class="abs sol-card" style="left:687px;top:1483px;width:246px;height:199px">
    <svg width="62" height="56" viewBox="0 0 62 56" fill="none" stroke="#0054AA" stroke-width="3"><circle cx="36" cy="22" r="14"/><circle cx="36" cy="22" r="6"/><path d="M4 50l10-18 10 18z"/></svg>
    <h3>Enterprise Risk Management</h3>
    <p>Holistic Risk Assessment And Capital Modeling That Integrates Across Business Units And Regulatory Frameworks.</p>
    <span class="go"><svg width="12" height="12" viewBox="0 0 24 24"><path d="M6 18L18 6M9 6h9v9" stroke="#fff" stroke-width="2.6" fill="none"/></svg></span>
  </div>
</section>

<!-- Characteristics -->
<section>
  <div class="abs pill" style="left:527px;top:1846px;width:152px;height:29px">WHY CHOOSE US</div>
  <h2 class="abs h2 center" style="top:1884px">Platform <b>Characteristics</b></h2>
  <p class="abs lead center" style="top:1940px">Key Attributes That Set Our Platform Apart In Delivering Reliable, Governance-Ready<br>Actuarial Analysis.</p>

  <svg class="abs" style="left:440px;top:2060px" width="320" height="180" viewBox="0 0 320 180" fill="none" stroke="#c6d3e3" stroke-width="1.5">
    <path d="M62 20 Q40 10 10 -5"/><path d="M258 20 Q280 10 310 -5"/>
    <path d="M62 160 Q40 170 10 185"/><path d="M258 160 Q280 170 310 185"/>
  </svg>
  <div class="abs hub"><div class="logo" style="font-size:24px"><span class="dot"></span>QP FIDUCIARY</div></div>
  <div class="abs node" style="left:496px;top:2075px"></div>
  <div class="abs node t" style="left:694px;top:2075px"></div>
  <div class="abs node t" style="left:496px;top:2212px"></div>
  <div class="abs node" style="left:694px;top:2212px"></div>

  <div class="abs ch-label" style="left:260px;top:2024px;width:106px;text-align:right">Structured<br>Workflows</div>
  <div class="abs ch-icon c-blue" style="left:382px;top:2010px"><svg width="38" height="38" viewBox="0 0 24 24" fill="none" stroke="#fff" stroke-width="1.8"><circle cx="12" cy="7" r="4"/><path d="M12 11v4M5 15h14M5 15v3M12 15v3M19 15v3"/></svg></div>
  <div class="abs ch-icon c-teal" style="left:748px;top:2010px"><svg width="38" height="38" viewBox="0 0 24 24" fill="none" stroke="#fff" stroke-width="1.8"><path d="M4 20V12M9 20V8M14 20V11M19 20V5M3 20h18"/></svg></div>
  <div class="abs ch-label" style="left:835px;top:2024px">Comparative<br>Analysis Capability</div>

  <div class="abs ch-label" style="left:210px;top:2228px;width:158px;text-align:right">Multi-Jurisdictional<br>Review Support</div>
  <div class="abs ch-icon c-teal" style="left:382px;top:2217px"><svg width="38" height="38" viewBox="0 0 24 24" fill="none" stroke="#fff" stroke-width="1.8"><circle cx="12" cy="9" r="5"/><path d="M3 18c3 0 5 2 9 2s6-2 9-3"/></svg></div>
  <div class="abs ch-icon c-blue" style="left:748px;top:2217px"><svg width="38" height="38" viewBox="0 0 24 24" fill="none" stroke="#fff" stroke-width="1.8"><path d="M2 12s4-6 10-6 10 6 10 6-4 6-10 6S2 12 2 12z"/><circle cx="12" cy="12" r="3"/></svg></div>
  <div class="abs ch-label" style="left:831px;top:2228px">Transparent<br>Assumptions</div>

  <div class="abs btn" style="left:451px;top:2331px;width:304px;height:44px">REQUEST A TECHNICAL WALKTHROUGH
    <span class="arr"><svg width="18" height="18" viewBox="0 0 24 24"><path d="M4 12h15M13 6l6 6-6 6" stroke="#0054AA" stroke-width="2.4" fill="none" stroke-linecap="round"/></svg></span></div>
</section>

<!-- Insights -->
<section>
  <div class="abs ins-bg"></div>
  <div class="abs pill" style="left:527px;top:2548px;width:103px;height:28px">INSIGHTS</div>
  <h2 class="abs h2 center" style="top:2584px">Insights &amp; Thought <b>Leadership</b></h2>
  <p class="abs lead center" style="top:2640px">Key Attributes That Set Our Platform Apart In Delivering Reliable, Governance-Ready<br>Actuarial Analysis.</p>

  <div class="abs slide" style="left:75px;top:2950px;border:1.5px solid #333"><svg width="16" height="16" viewBox="0 0 24 24"><path d="M20 12H5M11 6l-6 6 6 6" stroke="#333" stroke-width="2" fill="none"/></svg></div>
  <div class="abs slide" style="left:1089px;top:2950px;background:var(--blue-mid)"><svg width="16" height="16" viewBox="0 0 24 24"><path d="M4 12h15M13 6l6 6-6 6" stroke="#fff" stroke-width="2" fill="none"/></svg></div>

  <article class="abs post" style="left:142px;top:2702px">
    <div class="ph" role="img" aria-label="Business meeting beside a glowing lightbulb graphic" style="background:linear-gradient(135deg,#0c2f6b,#1d6fd1 60%,#0b2350)"></div>
    <div class="date"><i></i>24 JUL 2025</div>
    <h3>RBC (Risk-Based Capital)</h3>
    <p style="top:278px">Harbor Point, 24 July 2025 – QP Fiduciary is an independent actuarial consulting firm headquartered...</p>
    <div class="more">READ MORE</div>
  </article>
  <article class="abs post" style="left:456px;top:2702px">
    <div class="ph" role="img" aria-label="Hand pointing at financial price charts" style="background:linear-gradient(135deg,#3a3f4a,#8c929c 55%,#d66a4e)"></div>
    <div class="date"><i></i>13 JAN 2026</div>
    <h3>Evolution into Technology-Led Actuarial Platform</h3>
    <p style="top:299px">Harbor Point, January 12, 2026 – <u>QP Fiduciary</u> is thrilled...</p>
    <div class="more">READ MORE</div>
  </article>
  <article class="abs post" style="left:777px;top:2702px">
    <div class="ph" role="img" aria-label="Abstract graphic announcing new accounting standards" style="background:linear-gradient(135deg,#2b3036,#6d757e 55%,#c9ced3)"></div>
    <div class="date"><i></i>17 JAN 2025</div>
    <h3>IFRS 17: A Paradigm Shift For Insurers</h3>
    <p style="top:299px">Harbor Point, January 17, 2025 – <u>QP Fiduciary</u> is an actuarial consulting...</p>
    <div class="more">READ MORE</div>
  </article>

  <div class="abs btn" style="left:511px;top:3155px;width:180px;height:44px">VIEW ALL ARTICLES
    <span class="arr"><svg width="18" height="18" viewBox="0 0 24 24"><path d="M4 12h15M13 6l6 6-6 6" stroke="#0054AA" stroke-width="2.4" fill="none" stroke-linecap="round"/></svg></span></div>
</section>

<!-- Call to action -->
<section class="abs cta">
  <div class="cta-img" role="img" aria-label="Team reviewing financial reports and charts at a desk"></div>
  <div class="cta-fade"></div>
  <div class="pill-w">SCHEDULE A DEMO</div>
  <h2>Ready To Transform<br><b>Your Actuarial Practice?</b></h2>
  <p>Discover How QP Fiduciary's Platform Can Bring Structure, Transparency, And Confidence To Your Financial Analysis Workflows.</p>
  <div class="btn-w">REQUEST A TECHNICAL WALKTHROUGH
    <span class="arr"><svg width="18" height="18" viewBox="0 0 24 24"><path d="M4 12h15M13 6l6 6-6 6" stroke="#fff" stroke-width="2.4" fill="none" stroke-linecap="round"/></svg></span></div>
</section>

<!-- Footer -->
<footer class="abs footer">
  <div class="abs logo" style="left:142px;top:77px;color:#fff"><span class="dot"></span>QP FIDUCIARY</div>
  <p class="abs txt" style="left:142px;top:130px;width:220px">Common Approach To Service Delivery Cycle That Involves Defining The Problem, Designing A Solution And Monitoring The Results.</p>

  <h4 class="abs" style="left:469px;top:64px">Quick Links</h4>
  <div class="abs links" style="left:471px;top:96px">Company<br>Platform<br>Solutions<br>Insights<br>Contact</div>

  <h4 class="abs" style="left:664px;top:64px">Contact Details</h4>
  <div class="abs txt" style="left:664px;top:100px;width:200px;font-size:12.5px;line-height:1.7">
    <div style="display:flex;gap:8px"><svg width="13" height="16" viewBox="0 0 24 24" style="flex:none;margin-top:2px"><path d="M12 2a7 7 0 017 7c0 5-7 13-7 13S5 14 5 9a7 7 0 017-7z" fill="#fff"/><circle cx="12" cy="9" r="2.5" fill="#0b1a38"/></svg><span>410 Harbor Point Way,<br>Suite 200<br>Harbor Point, FL 30000</span></div>
    <div style="display:flex;gap:8px;margin-top:8px"><svg width="13" height="14" viewBox="0 0 24 24" style="flex:none;margin-top:3px"><path d="M5 3h4l2 5-3 2a12 12 0 006 6l2-3 5 2v4a2 2 0 01-2 2A18 18 0 013 5a2 2 0 012-2z" fill="#fff"/></svg><span>Phone<br>+1(555)010-4420</span></div>
    <div style="display:flex;gap:8px;margin-top:8px"><svg width="13" height="12" viewBox="0 0 24 24" style="flex:none;margin-top:4px"><rect x="2" y="5" width="20" height="14" fill="#fff"/><path d="M2 5l10 8 10-8" stroke="#0b1a38" stroke-width="2" fill="none"/></svg><span>Email<br>hello@qp-fiduciary.example</span></div>
  </div>

  <h4 class="abs" style="left:943px;top:64px">Social Media</h4>
  <div class="abs" style="left:941px;top:96px">
    <div class="soc"><span class="on"></span>Socialfeed</div>
    <div class="soc"><span></span>Videohub</div>
    <div class="soc"><span></span>Worknet</div>
    <div class="soc"><span></span>Photoline</div>
  </div>

  <div class="abs" style="left:142px;top:304px;width:916px;height:1px;background:rgba(255,255,255,.18)"></div>
  <div class="abs txt" style="left:142px;top:321px">© 2026 QP Fiduciary All Rights Reserved.</div>
  <div class="abs txt" style="left:844px;top:321px;width:214px;text-align:right">Price Policy Terms And Conditions</div>
</footer>

</body>
</html>
```